Kestrelwood Climate Business Card Design

Design new, 2 sides, business cards for a residential and light commercial heating, air conditioning contractor.

Target Market(s)

Homeowners, small businesses

Industry/Entity Type

Business

Contact Information for Business Card

Dominic Westerhall
Phone - 862-415-2736
Email
Address - PO box 518
Brightwater NJ 07912
Website - www.HarborBreezeLLC.example

Requirements
Must have
• logo, company colors, standard size with no die cut, so I can use nova stamp

```html
<!DOCTYPE html>
<html lang="en">
<head>
<meta charset="utf-8">
<title>Kestrelwood Climate Business Card</title>
<link href="https://fonts.googleapis.com/css2?family=Open+Sans:wght@400;600;700&display=swap" rel="stylesheet">
<style>
  :root {
    --crimson: #9b2335;
    --orange: #f29a1d;
    --ink: #4f4f52;
    --card: #ffffff;
    --backdrop: #e9e6e1;
  }
  * { box-sizing: border-box; margin: 0; padding: 0; }
  html, body { width: 1200px; height: 843px; overflow: hidden; }
  body {
    background: var(--backdrop);
    font-family: "Open Sans", Arial, sans-serif;
    position: relative;
  }
  .card {
    position: absolute;
    width: 540px;
    height: 309px;
    background: var(--card);
    box-shadow: 0 6px 18px rgba(0,0,0,.18);
    overflow: hidden;
  }
  .card-front { left: 70px; top: 130px; }
  .card-back { left: 590px; top: 404px; }

  .brand {
    position: absolute;
    left: 0; right: 0; top: 96px;
    display: flex;
    justify-content: center;
    align-items: center;
    gap: 12px;
  }
  .brand-dot {
    width: 24px; height: 24px;
    border-radius: 50%;
    background: var(--orange);
  }
  .brand-name {
    font-weight: 700;
    font-size: 34px;
    color: var(--crimson);
  }
  .tagline {
    position: absolute;
    left: 0; right: 0; top: 200px;
    text-align: center;
    font-size: 15px;
    line-height: 1.4;
    color: var(--ink);
    font-weight: 600;
  }

  .band {
    position: absolute;
    left: 0; top: 0;
    width: 540px; height: 104px;
    background: var(--crimson);
    border-bottom: 5px solid var(--orange);
  }
  .person {
    position: absolute;
    left: 0; right: 0; top: 32px;
    text-align: center;
    color: #fff;
  }
  .person-name { font-size: 19px; font-weight: 700; letter-spacing: .5px; }
  .person-title { font-size: 14px; font-weight: 400; }

  .contacts {
    position: absolute;
    left: 34px; right: 20px; top: 172px;
    color: var(--ink);
    font-size: 14.5px;
  }
  .contact-row { display: flex; gap: 16px; align-items: center; margin-bottom: 10px; }
  .contact-item { display: flex; align-items: center; gap: 5px; white-space: nowrap; }
  .icon { width: 14px; height: 14px; fill: var(--crimson); flex: none; }
</style>
</head>
<body>

<section class="card card-front" aria-label="Card front">
  <div class="brand">
    <span class="brand-dot"></span>
    <span class="brand-name">Kestrelwood Climate</span>
  </div>
  <p class="tagline">Residential and light commercial heating<br>Air conditioning contractor</p>
</section>

<section class="card card-back" aria-label="Card back">
  <div class="band"></div>
  <div class="person">
    <p class="person-name">MARA ELLISON</p>
    <p class="person-title">CEO/Founder</p>
  </div>

  <div class="contacts">
    <div class="contact-row">
      <span class="contact-item">
        <svg class="icon" viewBox="0 0 24 24"><path d="M6.6 10.8a15 15 0 0 0 6.6 6.6l2.2-2.2a1 1 0 0 1 1-.25 11.4 11.4 0 0 0 3.6.6 1 1 0 0 1 1 1V20a1 1 0 0 1-1 1A17 17 0 0 1 3 4a1 1 0 0 1 1-1h3.5a1 1 0 0 1 1 1c0 1.25.2 2.45.6 3.6a1 1 0 0 1-.25 1z"/></svg>
        862 415 2736
      </span>
      <span class="contact-item">
        <svg class="icon" viewBox="0 0 24 24"><path d="M7 1h10a2 2 0 0 1 2 2v18a2 2 0 0 1-2 2H7a2 2 0 0 1-2-2V3a2 2 0 0 1 2-2zm0 3v14h10V4zm5 15.5a1.2 1.2 0 1 0 0 2.4 1.2 1.2 0 0 0 0-2.4z"/></svg>
        862 390 5814
      </span>
      <span class="contact-item">
        <svg class="icon" viewBox="0 0 24 24"><path d="M6 2h10l2 2v5H6zM4 10h16a2 2 0 0 1 2 2v6h-4v4H6v-4H2v-6a2 2 0 0 1 2-2zm4 6v4h8v-4z"/></svg>
        862 415 2790
      </span>
    </div>
    <div class="contact-row">
      <span class="contact-item">
        <svg class="icon" viewBox="0 0 24 24"><path d="M2 5h20v14H2zm2 2v.5l8 5 8-5V7zm0 2.8V17h16V9.8l-8 5z"/></svg>
        mara@kestrelwood.example
      </span>
      <span class="contact-item">
        <svg class="icon" viewBox="0 0 24 24"><circle cx="12" cy="12" r="10"/><path d="M2 12h20M12 2c3 3 3 17 0 20M12 2c-3 3-3 17 0 20" stroke="#fff" stroke-width="1.5" fill="none"/></svg>
        www.KestrelwoodLLC.example
      </span>
    </div>
    <div class="contact-row">
      <span class="contact-item">PO box 518, Brightwater NJ 07912</span>
    </div>
  </div>
</section>

</body>
</html>
```